School Communication Email Template

Looking for a designer to create a couple simple email templates that are matching our brand colors and feel. Attached is the default email template that is currently being sent out. Company details can be shared upon request.

Template is to be used within the booking tool we use (snapshot below) and gmail. Template code is in HTML (see screenshot below).
Updates

Template code for website should be in HTML. Sorry if that created confusion.

Target Market(s)

Parents of kids enrolled in our classes

Industry/Entity Type

Kids sport classes

Font styles to use
Serif

Colors
0054AA
0677BA
7BADD7
CADEEF
E8F1F8
FFF300
FFF600
FEFA6F
FFFEC7
FFFEE8

Requirements
Must have
• Consistency with company brand/colors
Nice to have
• Flexibility to be adjusted as needed

```html
<!DOCTYPE html>
<html lang="en">
<head>
<meta charset="utf-8">
<title>Booking Confirmation Email</title>
<link rel="stylesheet" href="https://fonts.googleapis.com/css2?family=Arvo:wght@700&family=Poppins:wght@400;500;600&display=swap">
<style>
:root{
  --navy:#253b86;
  --white:#ffffff;
  --ink:#3f3f3f;
  --gold:#f8b927;
  --amber:#c98a2a;
  --sky:#65b9de;
  --sky-pale:#dff2fc;
  --sky-line:#b9e0f3;
  --frame:#c3cad8;
  --rule:#dcdcdc;
}
*{box-sizing:border-box;margin:0;padding:0}
html,body{width:1200px;height:2261px;overflow:hidden}
body{background:var(--navy);font-family:'Poppins',sans-serif;color:var(--ink);position:relative}
.abs{position:absolute}
.email{left:240px;top:46px;width:720px;height:2172px;background:var(--white)}
.brand-mark{left:335px;top:88px;width:110px;height:110px;border-radius:50%;background:var(--gold)}
.brand-name{left:269px;top:248px;width:245px;text-align:center;font-family:'Arvo',serif;font-weight:700;font-size:26px;line-height:34px;color:var(--navy);letter-spacing:.5px}
.sender{left:660px;top:120px;font-size:20px;line-height:29px}
.sender .sender-name{font-family:'Arvo',serif;font-weight:700;font-size:20px;color:var(--ink);margin-bottom:12px}
.divider{left:276px;top:347px;width:648px;height:2px;background:var(--rule)}
.headline{left:240px;top:394px;width:720px;text-align:center;font-family:'Arvo',serif;font-weight:700;font-size:29px;line-height:42px;color:var(--navy)}
.progress{left:340px;top:486px}
.greeting{left:258px;top:654px;font-size:18px;line-height:28px}
.greeting strong{color:var(--navy);font-weight:600}
.intro{left:260px;top:694px;width:672px;font-size:17.5px;line-height:29px}
.intro strong{font-weight:600;color:#333}
.details{left:300px;top:840px;width:598px;height:749px;border:2px solid var(--frame)}
.details-title{left:313px;top:856px;width:573px;height:89px;background:var(--navy);color:var(--white);font-family:'Arvo',serif;font-weight:700;font-size:30px;letter-spacing:1.5px;display:flex;align-items:center;justify-content:center}
.cell{width:276px;height:68px;display:flex;align-items:center;justify-content:center;font-size:18px}
.cell.label{background:var(--sky);color:var(--white);font-weight:600;font-size:19px}
.cell.value{background:var(--sky-pale);border:2px solid var(--sky-line);color:var(--ink)}
.changes{left:259px;top:1667px;width:680px;font-size:18px;line-height:30px}
.changes .ask{color:var(--navy);font-weight:600;font-size:19px}
.changes .manage-link{display:inline-block;margin-top:10px;color:var(--sky);font-weight:500;border-bottom:2px solid var(--sky);line-height:26px}
.changes .appt-id{margin-top:10px}
.changes .appt-id strong{font-weight:600}
.signoff{left:260px;top:1855px;font-size:18px;line-height:31px}
.signoff strong{color:var(--navy);font-weight:600;font-size:19px}
.footer-band{left:240px;top:1963px;width:720px;height:138px;background:var(--gold)}
.footer-addr{left:260px;top:1982px;font-size:16.5px;line-height:29px;color:#333}
.footer-addr strong{font-weight:600}
.footer-contact{left:626px;top:1984px;font-size:17px;line-height:29px;color:#333}
.social{top:2142px;width:44px;height:44px;border-radius:50%;background:var(--navy)}
</style>
</head>
<body>
<div class="abs email"></div>

<div class="abs brand-mark" aria-hidden="true"></div>
<div class="abs brand-name">COMPANY NAME</div>

<div class="abs sender">
  <div class="sender-name">YOUR COMPANY NAME</div>
  <div>418 Larkfield Rd, Brookvale</div>
  <div>Colorado 81009</div>
  <div>(719) 555-0142</div>
</div>

<div class="abs divider"></div>

<h1 class="abs headline">Your Booking has been confirmed</h1>

<svg class="abs progress" width="510" height="50" viewBox="0 0 510 50" aria-hidden="true">
  <line x1="31" y1="24" x2="455" y2="24" stroke="#c98a2a" stroke-width="2.5"/>
  <circle cx="31" cy="24" r="15" fill="#c98a2a"/>
  <circle cx="474" cy="25" r="20" fill="#fff" stroke="#c98a2a" stroke-width="2.5"/>
  <circle cx="474" cy="25" r="14" fill="#f8b927"/>
</svg>

<p class="abs greeting">Hello <strong>Mia Turner</strong></p>
<p class="abs intro">Your Booking confirmed with <strong>COMPANY NAME</strong>&nbsp; start date: <strong>21-02-2023</strong> and end date <strong>28-02-2023</strong>. Please find the details below.</p>

<div class="abs details"></div>
<div class="abs details-title">BOOKING DETAILS</div>

<div class="abs cell label" style="left:313px;top:960px">Student First Name</div>
<div class="abs cell label" style="left:610px;top:960px">Student Last Name</div>
<div class="abs cell value" style="left:313px;top:1039px">Mia</div>
<div class="abs cell value" style="left:610px;top:1039px">Turner</div>

<div class="abs cell label" style="left:313px;top:1116px">Appointment Name</div>
<div class="abs cell label" style="left:610px;top:1116px">Appointment Service</div>
<div class="abs cell value" style="left:313px;top:1194px">name of appointment</div>
<div class="abs cell value" style="left:610px;top:1194px">Service Name</div>

<div class="abs cell label" style="left:313px;top:1270px">Booking Start Date</div>
<div class="abs cell label" style="left:610px;top:1270px">Booking End Date</div>
<div class="abs cell value" style="left:313px;top:1348px">21st Feb, 2023</div>
<div class="abs cell value" style="left:610px;top:1348px">23rd Feb, 2023</div>

<div class="abs cell label" style="left:313px;top:1424px">Appointment Start Time</div>
<div class="abs cell label" style="left:610px;top:1424px">Appointment&nbsp; End Time</div>
<div class="abs cell value" style="left:313px;top:1502px">Morning 11.00 AM</div>
<div class="abs cell value" style="left:610px;top:1502px">Afternoon : 4:30 PM</div>

<div class="abs changes">
  <div class="ask">Need to make changes to this appointment?</div>
  <div>Manage or edit your appointment online through YOUR PORTAL NAME</div>
  <a class="manage-link">Manage My Appointment</a>
  <div class="appt-id"><strong>Appointmnet ID:</strong> ABCD123456</div>
</div>

<div class="abs signoff">
  <div>Thanks</div>
  <strong>Your Company Name</strong>
</div>

<div class="abs footer-band"></div>
<div class="abs footer-addr">
  <strong>Your Company Name</strong><br>
  418 Larkfield Rd, Brookvale,<br>
  Colorado 81009
</div>
<div class="abs footer-contact">
  (719) 555-0142<br>
  Info@yourcompany.com<br>
  www.yourcompany.com
</div>

<div class="abs social" style="left:513px" aria-label="Social profile"></div>
<div class="abs social" style="left:573px" aria-label="Social profile"></div>
<div class="abs social" style="left:646px" aria-label="Social profile"></div>
</body>
</html>
```